Harwick Moss Fine Art gallery website - Modern british art for sale

We need a website design that is both current and high end. Our products are expensive and this should be reflected in the look of the website. We would like the logo we had designed last year to be clearly seen in the design. We want sleek, simple, and easy to navigate. Nothing too colourful as the colours of the art should always take precedence.

Target Market(s)

The average price of one our products starts at £250 and can go up to £10,000 we are an entry level gallery.

Industry/Entity Type

Art Gallery

Number of Pages Required

5+ page

Font styles to use
Sans Serif

Colors
000000
ffffff
faa54b
abd037
886aae
b868aa

Requirements
Must have
• Attractive front page. Linked to our Social feed.
• 4 links from front page - New Releases, about us, Artists, contact us
• Social media links - Facebook, Social, YouTube, Instagram.
• Each artist must have their own page, each page must have a biography link to another page.
Nice to have
• Utilise our new logo design. I would like the Social feed to link to the front page in a small way so you can see what's being said on Social by the company. For future proofing maybe have a locations function on the front page which can be adroit down menu showing where our other galleries are.

```html
<!DOCTYPE html>
<html lang="en">
<head>
<meta charset="utf-8">
<title>Harwick Moss Fine Art</title>
<link href="https://fonts.googleapis.com/css2?family=Cinzel:wght@400;600&family=Jost:wght@400;500;600&display=swap" rel="stylesheet">
<style>
:root{
  --black:#000;
  --white:#fff;
  --orange:#faa54b;
  --purple:#886aae;
  --pink:#b868aa;
  --grey-band:#e8e8e8;
  --text:#333;
  --muted:#777;
  --sky-blue:#1da1f2;
  --gold:#d9b778;
  --gold-line:#c79a4a;
}
*{box-sizing:border-box;margin:0;padding:0}
html,body{width:670px;height:1200px;overflow:hidden;background:var(--white)}
body{position:relative;font-family:'Jost',sans-serif;color:var(--text)}
.abs{position:absolute}
.serif{font-family:'Cinzel',serif;font-variant:small-caps}
.accent{color:var(--orange)}

/* hero */
.hero{left:0;top:0;width:670px;height:419px;background:var(--black)}
.hero-photo{left:0;top:0}
.hero-title{left:92px;top:170px;color:var(--white);font-size:19px;line-height:21px;letter-spacing:.5px;font-weight:400}
.brand-box{left:431px;top:18px;width:98px;height:56px;border:2px solid var(--gold-line);background:#1b1b1b;display:flex;flex-direction:column;align-items:center;justify-content:center;text-align:center;color:var(--gold);font-family:'Cinzel',serif;font-size:8.5px;line-height:11px;letter-spacing:.8px}
.nav-rule{left:375px;top:89px;width:205px;height:1px;background:#444}
.main-nav{left:378px;top:95px;width:202px;display:flex;justify-content:space-between;font-size:7px;color:var(--white);letter-spacing:.3px}
.main-nav span.sep{color:#777}
.releases-title{right:90px;top:126px;color:var(--white);font-size:18px;letter-spacing:.5px;font-weight:400}
.releases-rule{left:520px;top:150px;width:60px;height:1px;background:#555}
.release{right:90px;width:210px;height:58px}
.release .thumb{right:0;top:0;width:58px;height:58px}
.release .info{right:70px;top:4px;width:140px;text-align:right;color:var(--white)}
.release .by{font-size:5px;letter-spacing:.3px;font-family:'Cinzel',serif}
.release .name{font-size:8.5px;letter-spacing:.5px;margin:2px 0 3px;font-family:'Cinzel',serif}
.release p{font-size:5.5px;line-height:8px;color:#ddd}

/* gallery */
.section-title{font-size:19px;color:var(--black);letter-spacing:.5px;font-weight:400}
.title-rule{height:1px;background:var(--pink);opacity:.6}
.gallery-title{left:0;width:670px;text-align:center;top:443px}
.gallery-card{top:494px;width:151px;height:110px;background:#f1f1f1;border:1px solid #ddd;border-radius:4px;box-shadow:0 1px 3px rgba(0,0,0,.15)}
.gallery-card .art{left:5px;top:5px}
.pin{width:7px;height:7px;border-radius:50%;background:var(--orange);border:1px solid #b77}
.gallery-meta{top:610px;font-size:5.5px;font-family:'Cinzel',serif;color:#333}
.gallery-name{top:619px;font-size:10px;font-family:'Cinzel',serif;color:#111;letter-spacing:.5px}
.arrow{top:552px}

/* artists */
.artists{left:0;top:658px;width:670px;height:210px;background:var(--grey-band)}
.artist-tile{width:107px;height:101px}
.artist-label{left:0;bottom:0;width:100%;height:20px;background:rgba(0,0,0,.55);color:var(--white);font-family:'Cinzel',serif;font-size:8px;letter-spacing:.5px;text-align:center;line-height:20px}
.artist-label.active{background:var(--orange)}
.artists-title{left:340px;top:674px;font-size:18px;color:var(--orange);font-weight:400}
.artists-copy{left:340px;width:234px;font-size:7.5px;line-height:10.5px;color:#333}
.bracket-btn{width:48px;height:20px;font-size:7px;color:var(--pink);display:flex;align-items:center;justify-content:center}
.bracket-btn svg{position:absolute;left:0;top:0}

/* about & feeds */
.about-title{left:90px;top:895px}
.about-copy{left:90px;top:932px;width:225px;font-size:7.6px;line-height:12.2px;color:#333}
.col-rule{left:334px;top:895px;width:1px;height:150px;background:#e3e3e3}
.feeds-title{left:354px;top:895px}
.tweet{left:357px;width:195px;height:40px}
.tweet .icon{left:0;top:0;width:25px;height:29px;border:1px solid #ccc;border-radius:2px;display:flex;align-items:center;justify-content:center}
.tweet .icon i{width:11px;height:11px;border-radius:50%;background:var(--sky-blue);display:block}
.tweet .body{left:36px;top:-1px;font-size:5.5px;line-height:7.5px;color:#222}
.tweet .body b{font-weight:600}
.tweet .ago{color:#555}
.tweet-rule{left:357px;width:195px;height:1px;background:#e6e6e6}
.side-tab{left:566px;top:973px;width:14px;height:50px;background:var(--sky-blue);border-radius:2px}

/* footer */
.footer-band{left:0;top:1092px;width:670px;height:33px;background:var(--orange)}
.footer-nav{left:90px;top:1104px;font-size:7px;color:var(--white);font-family:'Cinzel',serif;letter-spacing:.4px}
.footer-nav span{margin-right:7px}
.social{top:1100px;width:15px;height:15px;border-radius:50%;background:var(--white)}
.footer{left:0;top:1125px;width:670px;height:75px;background:var(--black)}
.contact-item{top:1144px;font-size:6.5px;line-height:9.5px;color:var(--white);white-space:nowrap}
.contact-item b{font-weight:500;font-size:6.5px;color:var(--white)}
.contact-icon{top:1145px;width:13px;height:13px;border-radius:50%;background:#444;display:flex;align-items:center;justify-content:center}
.news-input{left:463px;top:1155px;width:84px;height:12px;background:var(--white);font-size:5px;color:#666;padding-left:5px;line-height:12px}
.news-btn{left:547px;top:1155px;width:33px;height:12px;background:var(--orange);font-size:5.5px;color:#111;text-align:center;line-height:12px;font-weight:600}
.footer-rule{left:90px;top:1177px;width:490px;height:1px;background:#333}
.copyright{left:0;top:1183px;width:670px;text-align:center;font-size:6px;color:#ccc}
</style>
</head>
<body>

<!-- hero -->
<section class="hero abs">
  <svg class="hero-photo abs" width="400" height="419" role="img" aria-label="Mountain lake landscape photograph with red canoes in the foreground">
    <defs>
      <linearGradient id="heroGrad" x1="0" y1="0" x2="0" y2="1">
        <stop offset="0" stop-color="#d9d4c6"/>
        <stop offset=".25" stop-color="#8a8f96"/>
        <stop offset=".45" stop-color="#4f6b3c"/>
        <stop offset=".62" stop-color="#8aa8bd"/>
        <stop offset=".8" stop-color="#c9473a"/>
        <stop offset="1" stop-color="#b57a2e"/>
      </linearGradient>
    </defs>
    <polygon points="0,0 396,0 278,419 0,419" fill="url(#heroGrad)"/>
  </svg>
  <h1 class="hero-title abs serif">We are Art gallery<br>with Modern<br>British art</h1>

  <div class="brand-box abs"><span>Harwick Moss</span><span>Fine Art</span></div>
  <div class="nav-rule abs"></div>
  <nav class="main-nav abs serif"><span>New Releases</span><span class="sep">|</span><span>About us</span><span class="sep">|</span><span>Artists</span><span class="sep">|</span><span>Contact us</span></nav>

  <h2 class="releases-title abs serif">New <span class="accent">Releases</span></h2>
  <div class="releases-rule abs"></div>

  <article class="release abs" style="top:173px">
    <div class="info abs"><div class="by">Posted By : Alan</div><div class="name">Ashcombe Sitting Figures</div><p>Lorem ipsum dolor sit amet, consectetuer adipiscing elit, sed diam nonummy nibh euismod tincidunt ut</p></div>
    <svg class="thumb abs" width="58" height="58" role="img" aria-label="Ink sketch of seated figures"><rect width="58" height="58" fill="#e4e4e4"/></svg>
  </article>
  <article class="release abs" style="top:247px">
    <div class="info abs"><div class="by">Posted By : Alan</div><div class="name">Halden</div><p>Lorem ipsum dolor sit amet, consectetuer adipiscing elit, sed diam nonummy nibh euismod tincidunt ut</p></div>
    <svg class="thumb abs" width="58" height="58" role="img" aria-label="Grey print with a teal circular form"><rect width="58" height="58" fill="#9fa4a2"/></svg>
  </article>
  <article class="release abs" style="top:320px">
    <div class="info abs"><div class="by">Posted By : Alan</div><div class="name">Marlow Etching</div><p>Lorem ipsum dolor sit amet, consectetuer adipiscing elit, sed diam nonummy nibh euismod tincidunt ut</p></div>
    <svg class="thumb abs" width="58" height="58" role="img" aria-label="Black and white line etching"><rect width="58" height="58" fill="#cfcfcf"/></svg>
  </article>
</section>

<!-- gallery -->
<h2 class="section-title gallery-title abs serif">Art <span class="accent">Gallery</span></h2>
<div class="title-rule abs" style="left:323px;top:470px;width:68px"></div>

<svg class="arrow abs" style="left:58px" width="8" height="16"><polyline points="7,1 1,8 7,15" fill="none" stroke="#bbb" stroke-width="1.2"/></svg>
<svg class="arrow abs" style="left:604px" width="8" height="16"><polyline points="1,1 7,8 1,15" fill="none" stroke="#bbb" stroke-width="1.2"/></svg>

<div class="gallery-card abs" style="left:90px">
  <svg class="art abs" width="141" height="100" role="img" aria-label="Framed etching of a red and blue abstract form"><rect width="141" height="100" fill="#b98a4a"/><rect x="8" y="8" width="125" height="84" fill="#eef0ef"/></svg>
  <div class="pin abs" style="left:-3px;top:-3px"></div><div class="pin abs" style="right:-3px;bottom:-3px"></div>
</div>
<div class="gallery-card abs" style="left:258px">
  <svg class="art abs" width="141" height="100" role="img" aria-label="Grey print with a teal circular form"><rect width="141" height="100" fill="#9da09e"/></svg>
  <div class="pin abs" style="left:-3px;top:-3px"></div><div class="pin abs" style="right:-3px;bottom:-3px"></div>
</div>
<div class="gallery-card abs" style="left:425px">
  <svg class="art abs" width="141" height="100" role="img" aria-label="Black and white line etching"><rect width="141" height="100" fill="#d2d2d2"/></svg>
  <div class="pin abs" style="left:-3px;top:-3px"></div><div class="pin abs" style="right:-3px;bottom:-3px"></div>
</div>
<div class="gallery-meta abs" style="left:90px">Posted By : Alan | Posted in 10 Jan 2017</div>
<div class="gallery-name abs" style="left:90px">Vessel Etching</div>
<div class="gallery-meta abs" style="left:258px">Posted By : Alan | Posted in 10 Jan 2017</div>
<div class="gallery-name abs" style="left:258px">Halden</div>
<div class="gallery-meta abs" style="left:425px">Posted By : Alan | Posted in 10 Jan 2017</div>
<div class="gallery-name abs" style="left:425px">Marlow Etching</div>

<!-- artists -->
<section class="artists abs"></section>
<div class="artist-tile abs" style="left:94px;top:658px">
  <svg width="107" height="101" role="img" aria-label="Photo of a painter at his easel"><rect width="107" height="101" fill="#4d5a3e"/></svg>
  <div class="artist-label abs">Tom Ardley</div>
</div>
<div class="artist-tile abs" style="left:209px;top:658px">
  <svg width="107" height="101" role="img" aria-label="Photo of a young painter at a canvas"><rect width="107" height="101" fill="#a08464"/></svg>
  <div class="artist-label active abs">Tom Ardley</div>
</div>
<div class="artist-tile abs" style="left:94px;top:768px">
  <svg width="107" height="101" role="img" aria-label="Photo of an artist holding brushes"><rect width="107" height="101" fill="#3c4f74"/></svg>
  <div class="artist-label abs">Tom Ardley</div>
</div>
<div class="artist-tile abs" style="left:209px;top:768px">
  <svg width="107" height="101" role="img" aria-label="Photo of a painted wildlife canvas"><rect width="107" height="101" fill="#7a6547"/></svg>
  <div class="artist-label abs">Tom Ardley</div>
</div>

<h2 class="artists-title abs serif">Artists</h2>
<div class="title-rule abs" style="left:340px;top:699px;width:112px"></div>
<p class="artists-copy abs" style="top:716px">Lorem ipsum dolor sit amet, consectetuer adipiscing elit, sed diam nonummy nibh euismod tincidunt ut laoreet dolore magna aliquam erat volutpat.</p>
<p class="artists-copy abs" style="top:757px">Lorem ipsum dolor sit amet, consectetuer adipiscing elit, sed diam nonummy nibh euismod tincidunt ut laoreet dolore magna aliquam erat volutpat. Ut wisi enim ad minim veniam, quis nostrud exerci tation ullamcorper suscipit lobortis nisl ut aliquip ex ea commodo consequat. Duis autem vel eum iriure dolor in hendrerit in vulputate velit esse molestie consequat <span class="accent">... [+]</span></p>
<div class="bracket-btn abs" style="left:340px;top:830px">
  <svg width="48" height="20"><path d="M1 6V1h6M41 1h6v5M47 14v5h-6M7 19H1v-5" fill="none" stroke="var(--pink)" stroke-width="1"/></svg>VIEW ALL
</div>

<!-- about -->
<h2 class="section-title about-title abs serif">About <span class="accent">Us</span></h2>
<div class="title-rule abs" style="left:90px;top:920px;width:68px"></div>
<p class="about-copy abs">Lorem ipsum dolor sit amet, consectetuer adipiscing elit, sed diam nonummy nibh euismod tincidunt ut laoreet dolore magna aliquam erat volutpat. Ut wisi enim ad minim veniam, quis nostrud exerci tation ullamcorper suscipit lobortis nisl ut aliquip ex ea commodo consequat. Duis autem vel eum iriure dolor in hendrerit in vulputate velit esse molestie consequat, vel illum dolore eu feugiat nulla facilisis at vero eros et accumsan et iusto odio dignissim qui blandit praesent luptatum zzril delenit augue duis dolore .</p>
<div class="bracket-btn abs" style="left:90px;top:1040px;width:56px">
  <svg width="56" height="20"><path d="M1 6V1h6M49 1h6v5M55 14v5h-6M7 19H1v-5" fill="none" stroke="var(--pink)" stroke-width="1"/></svg>READ MORE
</div>

<div class="col-rule abs"></div>

<!-- feeds -->
<h2 class="section-title feeds-title abs serif">Social <span class="accent">Feeds</span></h2>
<div class="title-rule abs" style="left:354px;top:920px;width:68px"></div>

<div class="tweet abs" style="top:935px">
  <div class="icon abs"><i></i></div>
  <div class="body abs"><b>LOREM IPSUM</b> 02 feb , 2017<br>@Lorem ipsum dolor sit amet,<br>consectetuer <b>http://hm.example/ax41</b><br><span class="ago">40 minutes ago</span></div>
</div>
<div class="tweet-rule abs" style="top:975px"></div>
<div class="tweet abs" style="top:983px">
  <div class="icon abs"><i></i></div>
  <div class="body abs"><b>LOREM IPSUM</b> 02 feb , 2017<br>@Lorem ipsum dolor sit amet,<br>consectetuer <b>http://hm.example/ax41</b><br><span class="ago">40 minutes ago</span></div>
</div>
<div class="tweet-rule abs" style="top:1022px"></div>
<div class="tweet abs" style="top:1030px">
  <div class="icon abs"><i></i></div>
  <div class="body abs"><b>LOREM IPSUM</b> 02 feb , 2017<br>@Lorem ipsum dolor sit amet,<br>consectetuer <b>http://hm.example/ax41</b><br><span class="ago">40 minutes ago</span></div>
</div>
<div class="side-tab abs"></div>

<!-- footer -->
<div class="footer-band abs"></div>
<nav class="footer-nav abs"><span>New Releases</span><span>|</span><span>About us</span><span>|</span><span>Artists</span><span>|</span><span>Contact us</span></nav>
<div class="social abs" style="left:501px"></div>
<div class="social abs" style="left:522px"></div>
<div class="social abs" style="left:543px"></div>
<div class="social abs" style="left:564px"></div>

<footer class="footer abs"></footer>
<div class="contact-icon abs" style="left:92px"><svg width="7" height="9"><path d="M3.5 0a3 3 0 0 1 3 3c0 2.2-3 6-3 6s-3-3.8-3-6a3 3 0 0 1 3-3z" fill="#fff"/></svg></div>
<div class="contact-item abs" style="left:111px"><b>Harwick Moss Fine Art</b><br>123, Lorewam Dollar, Smit Amet - 123456</div>
<div class="contact-icon abs" style="left:256px"><svg width="8" height="8"><path d="M1 1l2-1 1.5 2.3-1 1a5 5 0 0 0 2.2 2.2l1-1L9 6 8 8C4 8 0 4 1 1z" fill="#fff"/></svg></div>
<div class="contact-item abs" style="left:275px"><b>Call Us :</b><br>+44 1632 960 214</div>
<div class="contact-icon abs" style="left:345px"><svg width="8" height="6"><rect x=".5" y=".5" width="7" height="5" fill="none" stroke="#fff"/><path d="M.5.5l3.5 3 3.5-3" fill="none" stroke="#fff"/></svg></div>
<div class="contact-item abs" style="left:364px"><b>Email Us :</b><br>info@harwickmossart.com</div>
<div class="contact-icon abs" style="left:445px"><svg width="8" height="6"><rect x=".5" y=".5" width="7" height="5" fill="none" stroke="#fff"/><path d="M.5.5l3.5 3 3.5-3" fill="none" stroke="#fff"/></svg></div>
<div class="contact-item abs" style="left:463px"><b>Subscribe to Our Newsletter</b></div>
<div class="news-input abs">Enter your email address</div>
<div class="news-btn abs">SUBMIT</div>
<div class="footer-rule abs"></div>
<div class="copyright abs">© 2016 Harwick Moss Fine Art. All Rights Reserved.</div>

</body>
</html>
```